professional business card design

Business card design. Photos have been uploaded and i am open to the designer choosing which photos to use. Would like the card to be mostyly in a grey scale design with black, whites, silver & grey colours. I have added copy of our flyer as would like on the back side of card our services to be listed. Do not use any bright colurs such as blue red green or yellow. i need to be able to edit the phone number and naem in the final card design submitted.

Target Market(s)

Clients

Industry/Entity Type

earhmovibng and transport

Contact Information for Business Card

Director Name, address, email, phone number and services

Colors

Designer to choose only greyscale colors for use in the design.

Requirements
Should not have
• no yellow, red, blue or green

```html
<!DOCTYPE html>
<html lang="en">
<head>
<meta charset="utf-8">
<title>Ironbark Pty Ltd – Business Card</title>
<link href="https://fonts.googleapis.com/css2?family=Rajdhani:wght@500;600;700&family=Roboto+Condensed:wght@400&family=Poppins:wght@500;600&display=swap" rel="stylesheet">
<style>
  :root {
    --page-bg: #e4e2de;
    --card-black: #050506;
    --card-grey: #232325;
    --silver: #c9c9cb;
    --white: #ffffff;
    --muted: #b5b5b8;
    --divider: #8a8a8d;
    --label-grey: #a9a9ad;
  }
  * { margin: 0; padding: 0; box-sizing: border-box; }
  html, body { width: 1200px; height: 1200px; overflow: hidden; background: var(--page-bg); }
  .canvas { position: relative; width: 1200px; height: 1200px; }

  .card {
    position: absolute;
    left: 239px;
    width: 723px;
    height: 412px;
    border-radius: 16px;
    background: var(--card-black);
    overflow: hidden;
    box-shadow: 0 3px 6px rgba(0,0,0,0.25);
  }
  .card--front { top: 140px; }
  .card--back { top: 645px; }

  .card__texture {
    position: absolute;
    left: 120px;
    top: 0;
    width: 483px;
    height: 100%;
    background: radial-gradient(ellipse 55% 45% at 50% 10%, #2b2b2e 0%, rgba(20,20,22,0.6) 55%, rgba(5,5,6,0) 100%),
                linear-gradient(90deg, rgba(5,5,6,0) 0%, var(--card-grey) 50%, rgba(5,5,6,0) 100%);
    opacity: 0.8;
  }

  .brand {
    position: absolute;
    text-align: center;
    font-family: "Rajdhani", sans-serif;
    font-weight: 700;
    color: var(--silver);
    line-height: 1;
  }
  .brand__name { display: block; font-size: 74px; letter-spacing: 2px; }
  .brand__suffix { display: block; font-size: 26px; margin-top: 14px; }
  .card--front .brand { left: 30px; top: 150px; width: 305px; }
  .card--back .brand { left: 0; top: 88px; width: 723px; }

  .divider {
    position: absolute;
    left: 361px;
    top: 114px;
    width: 2px;
    height: 175px;
    background: var(--divider);
  }

  .contact { position: absolute; left: 396px; top: 112px; font-family: "Rajdhani", sans-serif; }
  .contact__name { font-size: 31px; font-weight: 700; color: var(--white); letter-spacing: 1px; line-height: 1; }
  .contact__role { font-size: 22px; font-weight: 500; color: var(--muted); letter-spacing: 1px; margin-top: 4px; line-height: 1; }
  .contact__list { list-style: none; margin-top: 34px; }
  .contact__item { display: flex; align-items: center; height: 35px; font-size: 18px; font-weight: 500; color: var(--white); letter-spacing: 0.5px; }
  .contact__icon { width: 12px; height: 12px; margin: 0 14px 0 4px; fill: var(--white); }

  .services { position: absolute; left: 0; top: 236px; width: 723px; text-align: center; }
  .services__title {
    font-family: "Poppins", sans-serif;
    font-size: 15px;
    font-weight: 600;
    letter-spacing: 3.5px;
    color: var(--white);
    line-height: 1;
  }
  .services__title span { color: var(--label-grey); font-weight: 500; }
  .services__list {
    margin-top: 15px;
    font-family: "Roboto Condensed", sans-serif;
    font-size: 17px;
    color: var(--white);
    line-height: 23px;
  }
</style>
</head>
<body>
<main class="canvas">

  <section class="card card--front">
    <div class="card__texture" role="img" aria-label="Dark perforated metal texture background"></div>
    <div class="brand">
      <span class="brand__name">IRONBARK</span>
      <span class="brand__suffix">Pty Ltd</span>
    </div>
    <div class="divider"></div>
    <div class="contact">
      <h1 class="contact__name">Yourname Here</h1>
      <p class="contact__role">Designation</p>
      <ul class="contact__list">
        <li class="contact__item">
          <svg class="contact__icon" viewBox="0 0 24 24"><path d="M6.6 10.8c1.4 2.8 3.8 5.1 6.6 6.6l2.2-2.2c.3-.3.7-.4 1-.2 1.1.4 2.3.6 3.6.6.6 0 1 .4 1 1V20c0 .6-.4 1-1 1C10.6 21 3 13.4 3 4c0-.6.4-1 1-1h3.5c.6 0 1 .4 1 1 0 1.3.2 2.5.6 3.6.1.3 0 .7-.2 1L6.6 10.8z"/></svg>
          000-123-456-789
        </li>
        <li class="contact__item">
          <svg class="contact__icon" viewBox="0 0 24 24"><path d="M2 5h20v14H2V5zm2 2v.5l8 5 8-5V7H4z"/></svg>
          youremail@email.com
        </li>
        <li class="contact__item">
          <svg class="contact__icon" viewBox="0 0 24 24"><path d="M12 2a7 7 0 0 0-7 7c0 5.2 7 13 7 13s7-7.8 7-13a7 7 0 0 0-7-7zm0 9.5A2.5 2.5 0 1 1 12 6.5a2.5 2.5 0 0 1 0 5z"/></svg>
          123 St. Somewhere City
        </li>
      </ul>
    </div>
  </section>

  <section class="card card--back">
    <div class="card__texture" role="img" aria-label="Dark perforated metal texture background"></div>
    <div class="brand">
      <span class="brand__name">IRONBARK</span>
      <span class="brand__suffix">Pty Ltd</span>
    </div>
    <div class="services">
      <h2 class="services__title"><span>OUR</span> SERVICES</h2>
      <p class="services__list">
        Over size loads / Hot Shot Loads &nbsp;|&nbsp; Heavy Vehicle Recovery Services &nbsp;|&nbsp; Potable Water Deliveries<br>
        Road Building / Maintenance &nbsp;|&nbsp; Earthworks &nbsp;|&nbsp; Sand &nbsp;&amp; Metal Supply &amp; Cartage<br>
        Road Train Tippers &nbsp;|&nbsp; Road Train Tankers &nbsp;|&nbsp; Road Train Flat Tops &nbsp;|&nbsp; Drop Deck Trailers<br>
        Mine Site accredited equipment &amp; Operators
      </p>
    </div>
  </section>

</main>
</body>
</html>
```